Business Card for a Dental Office

The design should communicate integrity, quality and reliability. We also want the card look elegant, simple, but still stand out, different from the traditional-dental-office business card.

Industry/Entity Type

Business

```html
<!DOCTYPE html>
<html lang="en">
<head>
<meta charset="utf-8">
<title>Harlow Dental Centre – Stationery</title>
<link rel="stylesheet" href="https://fonts.googleapis.com/css2?family=Oswald:wght@500&family=Didact+Gothic&family=Open+Sans:wght@600&display=swap">
<style>
  :root{
    --backdrop:#3a3a3a;
    --paper:#f4f4f2;
    --ink:#111111;
    --night:#0b0b0b;
    --gold:#c9b21c;
    --gold-soft:#b9a52a;
    --rule:#333333;
    --muted:#2a2a2a;
  }
  *{margin:0;padding:0;box-sizing:border-box}
  html,body{width:1200px;height:900px;overflow:hidden;background:var(--backdrop)}
  .canvas{position:relative;width:1200px;height:900px}

  .card{position:absolute;width:560px;height:320px;background:var(--paper);overflow:hidden;
        box-shadow:0 10px 24px rgba(0,0,0,.45)}

  .brand{position:absolute;display:flex;align-items:center;gap:10px}
  .brand-mark{width:22px;height:22px;background:var(--gold)}
  .brand-name{font-family:'Oswald',sans-serif;font-weight:500;color:var(--ink);
              letter-spacing:.5px;line-height:1;text-transform:uppercase}
  .brand-tagline{font-family:'Open Sans',sans-serif;font-weight:600;color:var(--gold);
                 text-transform:uppercase;letter-spacing:1.2px;position:absolute}

  /* appointment card */
  .appointment{left:70px;top:80px}
  .appointment .brand{left:32px;top:30px}
  .appointment .brand-name{font-size:24px}
  .appointment .brand-tagline{left:64px;top:60px;font-size:8.5px}
  .appointment-title{position:absolute;right:30px;top:28px;font-family:'Oswald',sans-serif;
                     font-weight:500;color:var(--gold);font-size:20px;letter-spacing:1px}
  .appointment-rule{position:absolute;left:300px;right:30px;top:64px;border-top:1px solid var(--rule)}
  .field{position:absolute;font-family:'Didact Gothic',sans-serif;font-size:15px;color:var(--ink);
         display:flex;align-items:flex-end;gap:10px}
  .field .line{display:block;border-bottom:1px solid var(--rule);height:14px}
  .field-name{left:32px;top:112px}
  .field-name .line{width:220px}
  .field-time{left:320px;top:112px}
  .field-time .line{width:110px}
  .ampm{font-size:14px;letter-spacing:1px}
  .field-date{left:32px;top:160px}
  .field-date .line{width:250px}
  .days{position:absolute;left:32px;top:214px;display:flex;gap:22px;
        font-family:'Didact Gothic',sans-serif;font-size:13px;color:var(--ink)}
  .day{display:flex;align-items:center;gap:7px}
  .box{width:16px;height:16px;border:2px solid var(--ink)}
  .notice{position:absolute;left:32px;top:272px;font-family:'Didact Gothic',sans-serif;
          font-size:13.5px;color:var(--ink)}

  /* business card */
  .business{left:570px;top:490px;background:var(--night)}
  .business-top{position:absolute;left:0;top:0;width:100%;height:152px;background:var(--paper)}
  .business-notch{position:absolute;left:128px;top:150px}
  .business .brand{left:34px;top:62px}
  .business .brand-name{font-size:30px}
  .business .brand-tagline{left:66px;top:100px;font-size:10px}
  .person{position:absolute;right:34px;top:30px;text-align:right;font-family:'Didact Gothic',sans-serif;color:var(--ink)}
  .person-name{font-size:21px;letter-spacing:1px;font-weight:700;text-transform:uppercase}
  .person-role{font-size:13px;margin-top:2px}
  .address{position:absolute;right:30px;top:170px;text-align:right;font-family:'Didact Gothic',sans-serif;
           color:#fff;font-size:12.5px;line-height:1.45}
  .contacts{position:absolute;left:34px;top:200px;list-style:none;font-family:'Didact Gothic',sans-serif;
            color:#fff;font-size:13px}
  .contacts li{display:flex;align-items:center;gap:10px;height:20px}
  .contact-icon{width:15px;height:15px;border-radius:3px;background:var(--gold);display:flex;
                align-items:center;justify-content:center}
  .band{position:absolute;left:0;top:268px;width:100%;height:24px;
        background:linear-gradient(90deg,var(--gold-soft),var(--gold))}
</style>
</head>
<body>
<main class="canvas">

  <section class="card appointment" aria-label="Appointment card">
    <div class="brand"><span class="brand-mark"></span><span class="brand-name">Harlow Dental Centre</span></div>
    <p class="brand-tagline">Your smile is your gift to others</p>
    <h2 class="appointment-title">APPOINTMENT CARD</h2>
    <div class="appointment-rule"></div>

    <div class="field field-name">NAME <span class="line"></span></div>
    <div class="field field-time">TIME <span class="line"></span> <span class="ampm">AM&nbsp;&nbsp;PM</span></div>
    <div class="field field-date">DATE <span class="line"></span></div>

    <div class="days">
      <span class="day"><span class="box"></span>MON.</span>
      <span class="day"><span class="box"></span>TUES.</span>
      <span class="day"><span class="box"></span>WED.</span>
      <span class="day"><span class="box"></span>THUR.</span>
      <span class="day"><span class="box"></span>FRI.</span>
      <span class="day"><span class="box"></span>SAT.</span>
    </div>
    <p class="notice">If you are unable to keep your appointment, please call us within 24 hours.</p>
  </section>

  <section class="card business" aria-label="Business card">
    <div class="business-top"></div>
    <svg class="business-notch" width="20" height="10" viewBox="0 0 20 10"><polygon points="0,0 20,0 10,9" fill="var(--paper)"/></svg>

    <div class="brand"><span class="brand-mark"></span><span class="brand-name">Harlow Dental Centre</span></div>
    <p class="brand-tagline">Your smile is your gift to others</p>

    <div class="person">
      <p class="person-name">Morgan Ellis</p>
      <p class="person-role">General Manager</p>
    </div>

    <address class="address">27 Linden Avenue<br>Westbrook<br>GA 30000</address>

    <ul class="contacts">
      <li><span class="contact-icon"><svg width="9" height="9" viewBox="0 0 10 10"><path d="M2 1l2 2-1 1.5a6 6 0 0 0 2.5 2.5L7 6l2 2-1.5 1.5C4 9 1 6 .5 2.5z" fill="var(--night)"/></svg></span>(555) 014-2298</li>
      <li><span class="contact-icon"><svg width="10" height="8" viewBox="0 0 10 8"><rect x=".5" y=".5" width="9" height="7" fill="none" stroke="var(--night)"/><path d="M.5 .5L5 4.5 9.5 .5" fill="none" stroke="var(--night)"/></svg></span>info@harlowdc.com</li>
      <li><span class="contact-icon"><svg width="10" height="10" viewBox="0 0 10 10"><circle cx="5" cy="5" r="4.2" fill="none" stroke="var(--night)"/><ellipse cx="5" cy="5" rx="1.8" ry="4.2" fill="none" stroke="var(--night)"/><path d="M.8 5h8.4" stroke="var(--night)"/></svg></span>www.harlowdc.com</li>
    </ul>

    <div class="band"></div>
  </section>

</main>
</body>
</html>
```